New Company Business Card design

Looking for a corporate looking business card utilising my new logo design - the logo i would like embossed as one option and flat as another - simplistic but stylish - less is more - we are an import export business launching into the market - i would like a couple of options as main background - Grey or Black

```html
<!DOCTYPE html>
<html lang="en">
<head>
<meta charset="utf-8">
<title>Keelbridge Trading – Business Card</title>
<link rel="stylesheet" href="https://fonts.googleapis.com/css2?family=Roboto:wght@400;500&display=swap">
<style>
  :root {
    --stage: #d9d6d2;
    --card: #262626;
    --card-edge: #1c1c1c;
    --brand-blue: #1f7ac4;
    --text-light: #f2f2f2;
  }
  * { box-sizing: border-box; margin: 0; padding: 0; }
  html, body { width: 1200px; height: 419px; overflow: hidden; }
  body {
    background: var(--stage);
    font-family: "Roboto", Arial, sans-serif;
    display: flex;
    align-items: center;
    justify-content: center;
    gap: 80px;
  }
  .card {
    width: 460px;
    height: 264px;
    background: var(--card);
    border: 1px solid var(--card-edge);
    border-radius: 3px;
    box-shadow: 0 6px 18px rgba(0,0,0,.25);
    position: relative;
  }
  .card-front {
    display: flex;
    align-items: center;
    justify-content: center;
  }
  .brand {
    display: flex;
    align-items: center;
    gap: 12px;
  }
  .brand-dot {
    width: 34px; height: 34px;
    border-radius: 50%;
    background: var(--brand-blue);
  }
  .brand-name {
    color: var(--brand-blue);
    font-weight: 500;
    font-size: 24px;
    letter-spacing: .06em;
    text-transform: uppercase;
  }
  .card-back { padding: 38px 40px; color: var(--text-light); }
  .person-name {
    color: var(--brand-blue);
    font-size: 20px;
    font-weight: 500;
    text-transform: uppercase;
    letter-spacing: .02em;
  }
  .person-title {
    font-size: 13px;
    font-weight: 500;
    text-transform: uppercase;
    margin-top: 2px;
  }
  .address {
    font-size: 13px;
    line-height: 1.35;
    margin-top: 30px;
  }
  .contact-list { list-style: none; margin-top: 4px; }
  .contact-list li {
    display: flex;
    align-items: center;
    gap: 10px;
    font-size: 13px;
    line-height: 17px;
  }
  .contact-list svg { width: 11px; height: 11px; fill: var(--brand-blue); flex: none; }
</style>
</head>
<body>
  <section class="card card-front" aria-label="Card front">
    <div class="brand">
      <span class="brand-dot"></span>
      <span class="brand-name">Keelbridge Trading</span>
    </div>
  </section>

  <section class="card card-back" aria-label="Card back">
    <h1 class="person-name">Alex Morgan</h1>
    <p class="person-title">CEO/Founder</p>
    <p class="address">1420 Harbor View Road<br>Juneau, Alaska 99801</p>
    <ul class="contact-list">
      <li>
        <svg viewBox="0 0 12 12" aria-hidden="true"><path d="M2.5 1 4.5 1 5.2 3.6 4 4.6C4.6 6 6 7.4 7.4 8L8.4 6.8 11 7.5 11 9.5C11 10.3 10.3 11 9.5 11 5 11 1 7 1 2.5 1 1.7 1.7 1 2.5 1Z"/></svg>
        907 555 0142
      </li>
      <li>
        <svg viewBox="0 0 12 12" aria-hidden="true"><path d="M3 0h6a1 1 0 0 1 1 1v10a1 1 0 0 1-1 1H3a1 1 0 0 1-1-1V1a1 1 0 0 1 1-1Zm0 1.5v8h6v-8Z"/></svg>
        907 555 0187
      </li>
      <li>
        <svg viewBox="0 0 12 12" aria-hidden="true"><path d="M3 0h5v3H3ZM1 4h10v7H1Zm2 2v1h2V6Zm4 0v1h2V6ZM3 8v1h2V8Zm4 0v1h2V8Z"/></svg>
        907 555 0163
      </li>
      <li>
        <svg viewBox="0 0 12 12" aria-hidden="true"><path d="M0 2h12v1L6 7 0 3Zm0 2.2 6 4 6-4V10H0Z"/></svg>
        hello@keelbridge.com
      </li>
      <li>
        <svg viewBox="0 0 12 12" aria-hidden="true"><circle cx="6" cy="6" r="6"/></svg>
        www.keelbridge.com
      </li>
    </ul>
  </section>
</body>
</html>
```